Quillmere Supply Chain and Logistic Consulting

Please review the attached Business Card. I want as close to this card with the colors, fonts, and quality of the card as possible. The attached compass should replace the deer head on both sides of the card and the text should say:

Backside
Compass JPEG
Quillmere SC&L
A Supply Chain and Logistics Consulting Company

Frontside
Quillmere SC&L
Ray Falkner - Larkwood Bay
President
____________________________________
(555) 314-9027
QuillmereSCL@Examplemail.com
_____________________________________

Bottom Front Side

Target Market(s)

Businesses

Contact Information for Business Card

Backside
Compass JPEG
Quillmere SC&L

Frontside
Quillmere SC&L
President
(555) 314-9027
QuillmereSCL@Examplemail.com

Bottom Front Side

Font styles to use
Serif
Script

Colors

Designer to choose colors to be used in the design.

Requirements
Must have
• See attached card for reference
Nice to have
Should not have

```html
<!DOCTYPE html>
<html lang="en">
<head>
<meta charset="utf-8">
<title>Quillmere SC&amp;L — Business Cards</title>
<link rel="stylesheet" href="https://fonts.googleapis.com/css2?family=Cinzel:wght@400;600&family=Tinos&display=swap">
<style>
  :root {
    --stage: #101010;
    --card: #242424;
    --card-edge: #2c2c2c;
    --ink: #f2f2f2;
    --ink-muted: #7a7a7a;
    --mark-fill: #9a9a9a;
    --rule: #8a8a8a;
  }
  * { margin: 0; padding: 0; box-sizing: border-box; }
  html, body {
    width: 1200px; height: 900px; overflow: hidden;
    background: var(--stage);
  }
  .stage { position: relative; width: 1200px; height: 900px; }
  .card {
    position: absolute; left: 270px; width: 660px; height: 377px;
    background: linear-gradient(160deg, var(--card-edge), var(--card) 60%);
    box-shadow: 0 14px 30px rgba(0,0,0,.6);
    overflow: hidden;
  }
  .card--back { top: 50px; }
  .card--front { top: 473px; }

  .brand-mark {
    position: absolute; left: 200px; top: 40px;
    width: 130px; height: 130px; border-radius: 50%;
    background: var(--mark-fill);
  }

  .brand-name {
    position: absolute;
    font-family: "Cinzel", serif; font-weight: 400;
    color: var(--ink); letter-spacing: 1px; white-space: nowrap;
  }
  .card--back .brand-name { left: 290px; top: 205px; font-size: 27px; }
  .card--front .brand-name { left: 60px; top: 60px; font-size: 44px; }

  .tagline {
    position: absolute; left: 0; right: 0;
    font-family: "Cinzel", serif; font-size: 19px;
    color: var(--ink-muted); text-align: center; white-space: nowrap;
  }
  .card--back .tagline { top: 290px; }
  .card--front .tagline { top: 320px; }

  .holder {
    position: absolute; left: 0; width: 520px; text-align: center;
    font-family: "Tinos", serif; white-space: nowrap;
  }
  .holder__name { top: 140px; font-size: 25px; color: var(--ink); }
  .holder__role { top: 172px; font-size: 16px; color: var(--ink-muted); }

  .rule {
    position: absolute; left: 110px; width: 380px; height: 1px;
    background: linear-gradient(90deg, transparent, var(--rule), transparent);
  }
  .rule--top { top: 205px; }
  .rule--bottom { top: 285px; }

  .contact {
    position: absolute; left: 0; top: 215px; width: 600px; text-align: center;
    font-family: "Tinos", serif; font-size: 22px; color: var(--ink);
    line-height: 30px;
  }
</style>
</head>
<body>
<main class="stage">
  <section class="card card--back">
    <div class="brand-mark" aria-hidden="true"></div>
    <div class="brand-name">QUILLMERE SC&amp;L</div>
    <div class="tagline">A Supply Chain and Logistics Consulting Company</div>
  </section>

  <section class="card card--front">
    <div class="brand-name">QUILLMERE SC&amp;L</div>
    <div class="holder holder__name">Ray Falkner - Larkwood Bay</div>
    <div class="holder holder__role">President</div>
    <div class="rule rule--top"></div>
    <div class="contact">(555) 314-9027<br>QuillmereSCL@Examplemail.com</div>
    <div class="rule rule--bottom"></div>
    <div class="tagline">A Supply Chain and Logistics Consulting Company</div>
  </section>
</main>
</body>
</html>
```